TA BRAMLEY BUSINESS CARD DESIGN PROJECT

We need to utilize our logo that was expertly created on PixelHarbor and now need to match this with a business card design.

```html
<!DOCTYPE html>
<html lang="en">
<head>
<meta charset="utf-8">
<title>TA BRAMLEY – Business Card</title>
<link href="https://fonts.googleapis.com/css2?family=Montserrat:wght@400;500;700;800&display=swap" rel="stylesheet">
<style>
  :root {
    --brand-blue: #1155ad;
    --card-black: #141414;
    --card-white: #ffffff;
    --text-light: #f2f2f2;
    --page-bg: #d9dadc;
  }
  * { box-sizing: border-box; margin: 0; padding: 0; }
  html, body { width: 1200px; height: 900px; overflow: hidden; }
  body {
    background: var(--page-bg);
    font-family: "Montserrat", Arial, sans-serif;
    position: relative;
  }
  .card {
    position: absolute;
    left: 250px;
    width: 700px;
    height: 400px;
    border-radius: 22px;
    overflow: hidden;
    background: var(--card-white);
    box-shadow: 0 6px 18px rgba(0,0,0,0.18);
  }
  .card-front { top: 35px; }
  .card-back { top: 465px; }

  .brand-name {
    color: var(--brand-blue);
    font-weight: 800;
    letter-spacing: 0.12em;
    white-space: nowrap;
  }
  .card-front .brand-name {
    position: absolute;
    left: 0; right: 0; top: 50%;
    transform: translateY(-50%);
    text-align: center;
    font-size: 64px;
  }
  .card-front .brand-mark {
    position: absolute;
    left: 50%; top: 110px;
    width: 26px; height: 26px;
    margin-left: -13px;
    border-radius: 50%;
    background: var(--brand-blue);
  }

  .wave { position: absolute; inset: 0; }
  .card-back .brand-name {
    position: absolute;
    left: 40px; top: 120px;
    font-size: 34px;
  }
  .contact {
    position: absolute;
    right: 40px; top: 70px;
    text-align: right;
    color: var(--text-light);
    font-size: 15px;
    line-height: 1.45;
  }
  .contact-name {
    color: var(--brand-blue);
    font-weight: 700;
    font-size: 22px;
    letter-spacing: 0.02em;
    line-height: 1.1;
  }
  .contact-title { font-size: 15px; margin-bottom: 12px; }
  .name-block { position: relative; padding-right: 14px; margin-right: -14px; }
  .name-bar {
    position: absolute;
    right: -12px; top: 0;
    width: 8px; height: 46px;
    background: var(--brand-blue);
  }
  .contact-line { display: flex; justify-content: flex-end; align-items: center; gap: 8px; }
  .contact-line svg { width: 13px; height: 13px; fill: var(--brand-blue); flex: none; }
  .contact-line.no-icon { padding-right: 21px; }
  .address { margin-top: 12px; padding-right: 21px; }
</style>
</head>
<body>

<section class="card card-front">
  <span class="brand-mark"></span>
  <div class="brand-name">TA BRAMLEY</div>
</section>

<section class="card card-back">
  <svg class="wave" viewBox="0 0 700 400" width="700" height="400" aria-hidden="true">
    <path d="M560,0 C410,15 430,200 330,295 C255,365 170,385 60,400"
          fill="none" stroke="var(--brand-blue)" stroke-width="3"/>
    <path d="M592,0 C445,15 455,205 352,300 C275,370 190,390 110,400 L700,400 L700,0 Z"
          fill="var(--brand-blue)"/>
    <path d="M612,0 C468,22 470,215 368,308 C292,375 210,393 140,400 L700,400 L700,0 Z"
          fill="var(--card-white)"/>
    <path d="M622,0 C480,28 482,222 378,314 C304,380 225,396 160,400 L700,400 L700,0 Z"
          fill="var(--card-black)"/>
  </svg>

  <div class="brand-name">TA BRAMLEY</div>

  <div class="contact">
    <div class="name-block">
      <div class="contact-name">NORA QUILL</div>
      <div class="contact-title">Managing Director</div>
      <span class="name-bar"></span>
    </div>
    <div class="contact-line">123 456 789
      <svg viewBox="0 0 16 16"><path d="M3 1l3 3-2 2c1 2 3 4 5 5l2-2 3 3-2 3C7 15 1 9 0 3z"/></svg>
    </div>
    <div class="contact-line">123 456 789
      <svg viewBox="0 0 16 16"><rect x="4" y="0" width="8" height="16" rx="2"/></svg>
    </div>
    <div class="contact-line">info@yourmail.com
      <svg viewBox="0 0 16 16"><path d="M0 3h16v10H0z M0 3l8 6 8-6" /></svg>
    </div>
    <div class="contact-line">www.yourwebsite.com
      <svg viewBox="0 0 16 16"><circle cx="8" cy="8" r="8"/></svg>
    </div>
    <div class="address">Your address, City<br>State, Zip 1234</div>
  </div>
</section>

</body>
</html>
```